Create the Hero Image for a Classic Rock Documentary Pledgemint

Create the Key Art & Visual Identity for a Classic Rock Documentary Pledgemint
Project Overview

I'm preparing to launch a Pledgemint campaign for an ambitious documentary-style music project unlike anything I've seen before.

Over approximately 700 hours, I am systematically listening to the complete pre-1990 studio catalogs of 29 classic rock bands—316 albums in total. Every album receives three complete listens, detailed written commentary, numerical scoring, and is entered into a custom-built database before I determine my final rankings.

This is not a reaction channel.

It is not a "Top 10" list built from memory or nostalgia.

It is a documented investigation built on discipline, repetition, curiosity, and evidence.

The project's title has not yet been finalized, so this contest is not about designing a logo or complete brand identity. Instead, I am looking for the defining visual image that introduces the entire project to the world.

The Assignment

Design the key art for my Pledgemint campaign.

This image will become the visual centerpiece of the campaign and will likely be adapted for:

Pledgemint campaign
Vidoria banner
Social media
Posters
Printed promotional material
Future merchandise

Think of this as creating the movie poster for a documentary rather than a Vidoria thumbnail.

Creative Direction

I am looking for an image that communicates:

commitment
curiosity
discovery
obsession
thoughtful listening
the journey behind the rankings

The project is ultimately about earning an opinion through disciplined listening rather than simply having one.

The visual should feel cinematic, timeless, intelligent, and memorable.

I prefer subtle storytelling over obvious symbolism.

One of the defining visual elements of the project is an inexpensive portable suitcase-style record player. Its simplicity is intentional. The project isn't about expensive audio equipment or audiophile culture—it is about disciplined listening. A notebook, over-ear headphones, handwritten notes, and vinyl records are all appropriate visual elements if they help tell the story.

The image should communicate that ordinary tools—a portable record player, headphones, a notebook, and hundreds of hours of disciplined listening—can become the foundation of an extraordinary investigation.

Photography

The uploaded photographs are reference images only. They introduce me as the subject of the documentary and illustrate the walking and travel that have become part of the project's story.

Walking has become an important part of how I experience music, think through ideas, and visit places connected to classic rock history.

If your concept is selected, I will gladly create new photography—with the appropriate clothing, props, portable record player, headphones, notebook, and poses—to fully realize your vision.

Please judge the project primarily on the strength of the creative concept rather than the supplied photographs.

Setting

The environment should feel authentic to the project's story.

Possible themes include:

long-distance travel
iconic music locations
record collecting
discovery
listening
investigation
classic rock history
the personal journey behind the project

The setting should support the narrative rather than simply provide an attractive background.

Design Style

I gravitate toward sophisticated editorial design rather than loud commercial graphics.

Imagine something that could serve as the poster for a feature documentary.

Elegant typography.

Strong composition.

Atmosphere.

Restraint.

The image should make someone stop, look a second time, and ask:

"What is this project?"

Deliverables

Please submit:

One primary hero image
Any supporting concept notes that help explain your vision

Placeholder typography is perfectly acceptable.

The emphasis is on concept, storytelling, and visual impact—not polished production.

Future Opportunity

The winning designer will be invited to quote on a larger body of work for the same project, including:

Pledgemint graphics
Vidoria banner
Posters
Gatefold album package
Postcards
Certificates
PDF layouts
Additional promotional materials

I'm looking for a designer who can become the long-term visual partner for this project, not simply someone to complete a single assignment.
Updates

Authenticity is extremely important for this project. The audience for this documentary values craftsmanship and can be skeptical of artwork that has an obvious AI-generated appearance. Whatever tools you choose to use, the finished image should feel authentic, believable, and professionally crafted. Please avoid the common visual artifacts and overly polished, synthetic aesthetic often associated with AI imagery. The final artwork should feel like it was created by a graphic artist making thoughtful creative decisions, not generated by a machine.

Target Market(s)

Music lovers ages 35–70, classic rock fans, vinyl collectors, documentary viewers, Vidoria audiences, and Pledgemint backers who appreciate thoughtful long-form storytelling rather than clickbait.

Industry/Entity Type

Entertainment / Documentary / Vidoria / Music

Font styles to use
Serif

Requirements
Must have
• The image should immediately communicate that this is a serious, thoughtful music project. The central character should be me (reference photos attached). I should appear focused and deeply engaged in listening to music. Include a small, inexpensive portable record player with a vinyl record. Include over-ear headphones. The scene should create a subtle visual contradiction: an obsessive listener using humble equipment. The environment should tell a story and encourage viewers to look more closely. The artwork should be cinematic and suitable for use as Vidoria channel art and Pledgemint promotional material.
Nice to have
• Surprise me with an original environment that reflects discovery, travel, history, or music culture. The setting does not need to be realistic if it creates a compelling visual story. Strong use of lighting, atmosphere, depth, and composition. Hidden visual details that reward a second look. A design style that could become the visual identity for an entire documentary project.
Should not have
• No guitars, microphones, stages, amplifiers, or performing musicians. No generic recording studios. No DJ equipment. No stereotypical rock imagery (flames, skulls, leather jackets, electric guitars, etc.). Do not make the record player look expensive or luxurious. Avoid clutter. Avoid cartoon or comic-book styles.

```html
<!DOCTYPE html>
<html lang="en">
<head>
<meta charset="utf-8">
<title>Classic Rock Documentary – Key Art &amp; Campaign Preview</title>
<link rel="stylesheet" href="https://fonts.googleapis.com/css2?family=Bebas+Neue&family=Hind:wght@500;600;700&family=Inter:wght@400;500;600;700&display=swap">
<style>
  :root{
    --cream:#eeebe3;
    --ink:#0d0d0d;
    --rust:#6a2a0c;
    --slate:#3b3b3b;
    --photo-top:#4d5a35;
    --photo-mid:#6f6a45;
    --photo-low:#7a5a36;
    --page:#f7f7f5;
    --band:#f3efe6;
    --green:#05814a;
    --brand:#05ce78;
    --line:#e2e2de;
    --muted:#6b6b6b;
    --faint:#a9a9a9;
  }
  *{box-sizing:border-box;margin:0;padding:0}
  html,body{width:1037px;height:1200px;overflow:hidden;background:#fff}
  body{position:relative;font-family:"Inter",sans-serif;color:var(--ink)}

  /* ---------- Key art ---------- */
  .key-art{position:absolute;width:973px;height:551px;background:var(--cream);overflow:hidden;font-family:"Hind",sans-serif}
  .key-art--hero{left:32px;top:34px}
  .key-art svg.shapes{position:absolute;inset:0}
  .key-art .stats{position:absolute;right:42px;top:40px;text-align:right;color:var(--rust);font-weight:700;font-size:28px;line-height:29px;letter-spacing:.3px}
  .key-art .scope{position:absolute;right:35px;top:157px;text-align:right;color:var(--slate);font-weight:600;font-size:20.5px;line-height:22px;letter-spacing:.3px}
  .key-art .genre{position:absolute;right:38px;top:318px;text-align:right;color:var(--cream);font-family:"Bebas Neue",sans-serif;font-size:60px;line-height:52px;letter-spacing:1px}
  .key-art .title-slot{position:absolute;right:38px;top:428px;text-align:right;color:#fff;font-weight:700;font-size:34px;line-height:40px;letter-spacing:.3px}
  .key-art .effort{position:absolute;left:26px;top:410px;color:var(--ink);font-weight:700;font-size:24px;line-height:27px}
  .key-art .effort .miles{display:block;margin-left:6px;margin-bottom:17px}

  /* ---------- Campaign preview ---------- */
  .preview-bar{position:absolute;left:39px;top:612px;display:flex;align-items:center;gap:7px;font-size:6.6px;color:#333}
  .preview-bar .brand{font-family:"Inter",sans-serif;font-weight:700;font-size:9px;color:var(--brand);letter-spacing:.2px}
  .preview-bar a{color:var(--green);text-decoration:underline}
  .preview-rule{position:absolute;left:35px;top:635px;width:974px;height:1px;background:var(--line)}

  .project-head{position:absolute;left:35px;top:636px;width:972px;height:331px;background:var(--page)}
  .project-title{position:absolute;left:0;width:1283px;top:657px;text-align:center;font-weight:600;font-size:12.5px}
  .project-sub{position:absolute;left:0;width:1283px;top:675px;text-align:center;font-size:8.6px;color:#333}

  .video-frame{position:absolute;left:341px;top:704px;width:395px;height:225px;border:1px solid var(--ink);overflow:hidden;background:var(--cream)}
  .video-frame .key-art{left:0;top:0;transform:scale(.406,.408);transform-origin:0 0}

  .meta{position:absolute;top:935px;display:flex;align-items:center;gap:4px;font-size:6px;color:#222}
  .meta--category{left:341px}
  .meta--place{left:401px}

  .stats-col{position:absolute;left:752px;top:708px;width:188px}
  .progress{height:3px;background:#e4e4e1;border-radius:2px}
  .figure{font-weight:700;font-size:14px;line-height:16px;margin-top:12px}
  .figure--plain{font-weight:500;color:#555;font-size:13px;margin-top:7px}
  .figure-label{font-size:6.8px;color:#666;margin-top:1px}
  .back-btn{margin-top:12px;height:21px;background:var(--green);color:#fff;font-size:7.6px;display:flex;align-items:center;justify-content:center}
  .actions{margin-top:8px;display:flex;align-items:center;gap:8px}
  .remind{width:92px;height:20px;border:1px solid #ddd;background:#fff;display:flex;align-items:center;justify-content:center;gap:4px;font-size:6.3px}
  .share-dot{width:10px;height:10px;border-radius:50%;background:#333}
  .fine{margin-top:10px;font-size:5.4px;line-height:8px;color:#333}
  .fine u{font-weight:600}

  .promise-band{position:absolute;left:32px;top:967px;width:974px;height:79px;background:var(--band)}
  .promise{position:absolute;top:988px;display:flex;gap:7px;font-size:8.8px;line-height:11.5px;color:#333}
  .promise .badge{flex:none;width:14px;height:14px;border-radius:50%;margin-top:2px}
  .promise--one{left:352px}.promise--one .badge{background:#8f82e6}
  .promise--two{left:556px}.promise--two .badge{background:#f4cf2a}
  .promise--three{left:760px;top:991px}.promise--three .badge{background:#3dd38d}

  .tabs{position:absolute;left:342px;top:1054px;display:flex;font-size:6.8px}
  .tabs span{margin-right:22px;color:#222}
  .tabs .active{font-weight:600}
  .tabs .off{color:var(--faint)}
  .tab-rule{position:absolute;left:32px;top:1076px;width:974px;height:1px;background:var(--line)}
  .tab-mark{position:absolute;left:340px;top:1074px;width:38px;height:2px;background:#222}

  .side-link{position:absolute;left:346px;top:1100px;font-size:6.5px;font-weight:600}
  .story{position:absolute;left:450px;top:1099px;font-size:15px;font-weight:400}
  .support{position:absolute;left:764px;top:1102px;font-size:10px}
  .pledge-box{position:absolute;left:764px;top:1126px;width:162px;height:60px;border:1px solid var(--line);border-bottom:none;background:#fff;padding:8px 9px}
  .pledge-box .lead{font-size:8.8px;color:#222}
  .pledge-box .label{margin-top:15px;font-size:6px;color:#333}
  .pledge-box .field{margin-top:3px;height:1px;background:var(--line)}
</style>
</head>
<body>

<!-- Key art -->
<section class="key-art key-art--hero">
  <svg class="shapes" width="973" height="551" viewBox="0 0 973 551">
    <defs>
      <linearGradient id="photoTone" x1="0" y1="0" x2="0.3" y2="1">
        <stop offset="0" stop-color="#3f4c2c"/>
        <stop offset="0.45" stop-color="#5d6440"/>
        <stop offset="1" stop-color="#7a5a36"/>
      </linearGradient>
    </defs>
    <path role="img" aria-label="Photograph of the documentary's host walking with a backpack through an old cemetery among trees" fill="url(#photoTone)" d="M0 0 L395 0 L420 12 L500 8 L520 40 L505 70 L545 100 L525 160 L575 178 L560 230 L600 250 L580 300 L600 318 L540 370 L565 420 L520 470 L530 520 L500 551 L0 551 Z"/>
    <path fill="var(--cream)" d="M0 418 L40 398 L95 390 L140 372 L210 378 L260 368 L330 392 L345 440 L318 470 L350 480 L320 505 L390 522 L330 540 L300 551 L0 551 Z"/>
    <path fill="var(--ink)" d="M620 250 L700 238 L760 250 L840 232 L973 238 L973 551 L690 551 L700 530 L610 520 L575 490 L545 470 L500 430 L475 410 L535 395 L520 370 L590 350 L560 330 L610 300 L585 278 Z"/>
  </svg>
  <div class="stats">700 HOURS<br>29 CLASSIC ROCK BANDS<br>316 ALBUMS</div>
  <div class="scope">A DEEP DIVE INTO THE COMPLETE<br>PRE-1990 STUDIO CATALOGS</div>
  <div class="genre">CLASSIC ROCK<br>DOCUMENTARY</div>
  <div class="title-slot">TITLE NAME<br>PLACEHOLDER</div>
  <div class="effort"><span class="miles">XX MILES WALKED</span>XX MONTHS OF<br>SUSTAINED EFFORT AND<br>CAREFUL EXPLORATION</div>
</section>

<!-- Campaign preview -->
<div class="preview-bar"><span class="brand">Pledgemint</span><span><a>Enable sharing</a> to send this preview to others and gather feedback.</span></div>
<div class="preview-rule"></div>
<div class="project-head"></div>
<div class="project-title">700 Hours, 29 Bands, 1 Database.</div>
<div class="project-sub">The albums that raised us, finally put to the test.</div>

<div class="video-frame">
  <section class="key-art">
    <svg class="shapes" width="973" height="551" viewBox="0 0 973 551">
      <defs>
        <linearGradient id="photoToneSmall" x1="0" y1="0" x2="0.3" y2="1">
          <stop offset="0" stop-color="#3f4c2c"/>
          <stop offset="0.45" stop-color="#5d6440"/>
          <stop offset="1" stop-color="#7a5a36"/>
        </linearGradient>
      </defs>
      <path role="img" aria-label="Photograph of the documentary's host walking through an old cemetery" fill="url(#photoToneSmall)" d="M0 0 L395 0 L420 12 L500 8 L520 40 L505 70 L545 100 L525 160 L575 178 L560 230 L600 250 L580 300 L600 318 L540 370 L565 420 L520 470 L530 520 L500 551 L0 551 Z"/>
      <path fill="var(--cream)" d="M0 418 L40 398 L95 390 L140 372 L210 378 L260 368 L330 392 L345 440 L318 470 L350 480 L320 505 L390 522 L330 540 L300 551 L0 551 Z"/>
      <path fill="var(--ink)" d="M620 250 L700 238 L760 250 L840 232 L973 238 L973 551 L690 551 L700 530 L610 520 L575 490 L545 470 L500 430 L475 410 L535 395 L520 370 L590 350 L560 330 L610 300 L585 278 Z"/>
    </svg>
    <div class="stats">700 HOURS<br>29 CLASSIC ROCK BANDS<br>316 ALBUMS</div>
    <div class="scope">A DEEP DIVE INTO THE COMPLETE<br>PRE-1990 STUDIO CATALOGS</div>
    <div class="genre">CLASSIC ROCK<br>DOCUMENTARY</div>
    <div class="title-slot">TITLE NAME<br>PLACEHOLDER</div>
    <div class="effort"><span class="miles">XX MILES WALKED</span>XX MONTHS OF<br>SUSTAINED EFFORT AND<br>CAREFUL EXPLORATION</div>
  </section>
</div>

<div class="meta meta--category">
  <svg width="8" height="8" viewBox="0 0 8 8"><circle cx="4" cy="4" r="3.4" fill="none" stroke="#222" stroke-width=".8"/><path d="M5.4 2.6 L4.5 4.5 L2.6 5.4 L3.5 3.5 Z" fill="#222"/></svg>
  Documentary
</div>
<div class="meta meta--place">
  <svg width="7" height="9" viewBox="0 0 7 9"><path d="M3.5 0.5 A3 3 0 0 1 6.5 3.5 C6.5 5.5 3.5 8.5 3.5 8.5 C3.5 8.5 0.5 5.5 0.5 3.5 A3 3 0 0 1 3.5 0.5 Z" fill="#222"/><circle cx="3.5" cy="3.4" r="1.1" fill="#fff"/></svg>
  San Jose, CA
</div>

<aside class="stats-col">
  <div class="progress"></div>
  <div class="figure">$0</div>
  <div class="figure-label">pledged of $5,000 goal</div>
  <div class="figure figure--plain">0</div>
  <div class="figure-label">backers</div>
  <div class="figure figure--plain">30</div>
  <div class="figure-label">days to go</div>
  <div class="back-btn">Back this project</div>
  <div class="actions">
    <div class="remind">
      <svg width="6" height="7" viewBox="0 0 6 7"><path d="M1 .5 H5 V6.5 L3 5 L1 6.5 Z" fill="none" stroke="#222" stroke-width=".8"/></svg>
      Remind me
    </div>
    <span class="share-dot"></span>
    <span class="share-dot"></span>
    <span class="share-dot"></span>
    <svg width="10" height="8" viewBox="0 0 10 8"><rect x=".5" y=".5" width="9" height="7" rx="1" fill="none" stroke="#333" stroke-width=".8"/><path d="M.8 1 L5 4.5 L9.2 1" fill="none" stroke="#333" stroke-width=".8"/></svg>
    <svg width="10" height="8" viewBox="0 0 10 8"><rect x=".5" y=".5" width="9" height="7" rx="1" fill="none" stroke="#333" stroke-width=".8"/><path d="M3.5 2.5 L2 4 L3.5 5.5 M6.5 2.5 L8 4 L6.5 5.5" fill="none" stroke="#333" stroke-width=".8"/></svg>
  </div>
  <p class="fine"><u>All or nothing.</u> This project will only be funded if it reaches its goal by the campaign deadline.</p>
</aside>

<div class="promise-band"></div>
<div class="promise promise--one"><span class="badge"></span><p>Pledgemint connects creators with<br>backers to fund projects.</p></div>
<div class="promise promise--two"><span class="badge"></span><p>Rewards aren’t guaranteed, but<br>creators must regularly update backers.</p></div>
<div class="promise promise--three"><span class="badge"></span><p>You’re only charged if the project meets<br>its funding goal by the campaign<br>deadline.</p></div>

<nav class="tabs">
  <span class="active">Campaign</span>
  <span>Rewards</span>
  <span>Creator</span>
  <span>FAQ</span>
  <span class="off">Updates</span>
  <span class="off">Comments</span>
  <span class="off">Community</span>
</nav>
<div class="tab-rule"></div>
<div class="tab-mark"></div>

<div class="side-link">Risks</div>
<h2 class="story">Story</h2>
<div class="support">Support</div>
<div class="pledge-box">
  <div class="lead">Make a pledge without a reward</div>
  <div class="label">Pledge amount</div>
  <div class="field"></div>
</div>

</body>
</html>
```